Business card design for holistic health care clinic

We need a double-sided business card design for our holistic health care clinic that integrates our logo design and also its color scheme. My business is called Valmira. It is an integrative medicine clinic. You have already done the logo for me. Please ensure an elegant and upscale design that is not cluttered, but still has all the necessary information (please see below for details).

Target Market(s)

Wellness, fitness, rehabilitation for educated, well-traveled open-minded clients who are focused on natural, organic, balanced and preventive healthcare and lifestyle.

Industry/Entity Type

Medical

Contact Information for Business Card

Modern, clean.

Number of Pages Required

1 page

Font styles to use
Serif
Sans Serif

Colors

Designer to choose colors to be used in the design.

Requirements
Must have
• Logo on one side, all other information on the other side.
• Other information should include:
• Tobias Wrenfeld - DOE, CPT, LMT
• 4100 East Marrow Drive
• Austin, TX 78119
• 512 555 0148
• 818 555 0192
• info@ValmiraHealth.example
• t.wrenfeld@ValmiraHealth.example
Nice to have
• Darker background on front - but not totally black - shaded/dark gray.

```html
<!DOCTYPE html>
<html lang="en">
<head>
<meta charset="utf-8">
<title>Valmira – Business Card</title>
<link href="https://fonts.googleapis.com/css2?family=Montserrat:wght@300;400;700&display=swap" rel="stylesheet">
<style>
  :root{
    --canvas:#1b1b1b;
    --card-dark:#2b2b2b;
    --card-light:#ffffff;
    --brand-blue:#1590d2;
    --text-light:#e6e6e6;
  }
  *{box-sizing:border-box;margin:0;padding:0}
  html,body{width:1200px;height:852px;overflow:hidden}
  body{
    background:var(--canvas);
    font-family:"Montserrat",Arial,sans-serif;
    display:flex;align-items:center;justify-content:center;gap:40px;
  }
  .card{
    position:relative;width:550px;height:314px;border-radius:18px;overflow:hidden;
  }
  .card--front{background:var(--card-dark)}
  .card--back{background:var(--card-light)}

  .brand{
    position:absolute;left:0;right:0;display:flex;flex-direction:column;align-items:center;
  }
  .brand__row{display:flex;align-items:center;gap:12px}
  .brand__dot{width:22px;height:22px;border-radius:50%;background:var(--brand-blue)}
  .brand__name{
    font-weight:700;color:var(--brand-blue);font-size:62px;letter-spacing:1px;line-height:1;
  }
  .brand__tagline{
    margin-top:6px;font-weight:700;color:var(--brand-blue);font-size:17px;letter-spacing:.3px;
  }
  .card--front .brand{top:104px}
  .card--back .brand{top:44px}
  .card--back .brand__name{font-size:52px}
  .card--back .brand__tagline{font-size:14px}

  .info-band{position:absolute;left:0;top:0;width:550px;height:314px}
  .info-band path{fill:var(--card-dark)}

  .person{position:absolute;left:40px;top:226px;color:var(--text-light)}
  .person__name{
    font-weight:700;color:var(--brand-blue);font-size:22px;text-transform:uppercase;letter-spacing:.3px;
  }
  .person__creds{font-weight:300;font-size:12px;margin-top:3px}
  .person__address{font-weight:300;font-size:12px;margin-top:10px;line-height:1.45}

  .contact{
    position:absolute;right:24px;top:196px;list-style:none;color:var(--text-light);
    font-weight:300;font-size:12.5px;line-height:1.6;text-align:right;
  }
  .contact li{display:flex;align-items:center;justify-content:flex-end;gap:10px}
  .contact svg{width:11px;height:11px;flex:none}
  .contact svg *{stroke:var(--brand-blue);fill:none;stroke-width:1.6}
</style>
</head>
<body>

  <section class="card card--front" aria-label="Card front">
    <div class="brand">
      <div class="brand__row">
        <span class="brand__dot"></span>
        <span class="brand__name">VALMIRA</span>
      </div>
      <span class="brand__tagline">Integrative Holistic Medicine</span>
    </div>
  </section>

  <section class="card card--back" aria-label="Card back">
    <div class="brand">
      <div class="brand__row">
        <span class="brand__dot"></span>
        <span class="brand__name">VALMIRA</span>
      </div>
      <span class="brand__tagline">Integrative Holistic Medicine</span>
    </div>

    <svg class="info-band" viewBox="0 0 550 314" aria-hidden="true">
      <path d="M0,210 L34,210 L46,192 L48,210 L550,160 L550,314 L0,314 Z"/>
    </svg>

    <div class="person">
      <div class="person__name">Tobias Wrenfeld</div>
      <div class="person__creds">DOE, CPT, LMT</div>
      <div class="person__address">4100 East Marrow Drive<br>Austin, TX 78119</div>
    </div>

    <ul class="contact">
      <li>512 555 0148
        <svg viewBox="0 0 12 12"><path d="M2 1 L4 1 L5 4 L3.5 5 Q5 8 7 8.5 L8 7 L11 8 L11 10 Q10 11 8 11 Q1 9 1 2 Z"/></svg>
      </li>
      <li>818 555 0192
        <svg viewBox="0 0 12 12"><rect x="3" y="1" width="6" height="10" rx="1"/></svg>
      </li>
      <li>info@ValmiraHealth.example
        <svg viewBox="0 0 12 12"><rect x="1" y="2.5" width="10" height="7"/><path d="M1 2.5 L6 6.5 L11 2.5"/></svg>
      </li>
      <li>t.wrenfeld@ValmiraHealth.example
        <svg viewBox="0 0 12 12"><circle cx="6" cy="6" r="5"/><path d="M1 6 H11 M6 1 Q3 6 6 11 Q9 6 6 1"/></svg>
      </li>
    </ul>
  </section>

</body>
</html>
```